50th Anniversary Gala Save the date Postcard 8.5x5.5 inches

Looking for a 5.5x8.5 in one-sided postcard design for our annual gala. Design needs to include "Save the date" prominently with all the event information included below. Design should be light, include the colors of our logo and elegant. (almost like a wedding save the date). "Threads of Grace" should look like its own logo.

50th Anniversary Gala at The Lodge at Marrow Glen – “Threads of Grace – Celebrating 50 Years of Building Community”
Thursday, October 24
6-11p
The Lodge at Marrow Glen
Sallow Brook Road, Larkhaven, NY
Honoring – TWR Previous Presidents

Target Market(s)

Exisiting donors

Industry/Entity Type

nonprofit

Font styles to use
Serif
Script

Requirements
Must have
• Save the date prominent
Should not have
• should not have a dark background

```html
<!DOCTYPE html>
<html lang="en">
<head>
<meta charset="utf-8">
<title>50th Anniversary Gala – Save the Date</title>
<link rel="stylesheet" href="https://fonts.googleapis.com/css2?family=Allura&family=Poppins:wght@400;500;600;700&display=swap">
<style>
  :root {
    --page: #ffffff;
    --card: #ffffff;
    --sky: #1b8fd2;
    --navy: #1b4a8c;
    --ink: #1d1d2b;
    --gold: #d49b2f;
    --green: #6fab3f;
    --wash-light: #d9ecf5;
    --wash-mid: #a9d2ec;
    --wash-deep: #4f8dcb;
  }
  * { margin: 0; padding: 0; box-sizing: border-box; }
  html, body { width: 800px; height: 1200px; overflow: hidden; background: var(--page); }
  body { position: relative; font-family: "Poppins", sans-serif; color: var(--ink); }

  .postcard {
    position: absolute; left: 30px; top: 360px;
    width: 740px; height: 479px;
    background: var(--card);
    overflow: hidden;
    box-shadow: 0 10px 24px rgba(0,0,0,0.28);
  }
  .wash { position: absolute; }
  .wash-left {
    left: -60px; top: 0; width: 300px; height: 479px;
    background: radial-gradient(ellipse at 20% 70%, var(--wash-light) 0%, rgba(217,236,245,0.5) 45%, rgba(255,255,255,0) 75%);
  }
  .wash-top-right {
    right: -40px; top: -40px; width: 220px; height: 260px;
    background: radial-gradient(ellipse at 75% 25%, var(--wash-mid) 0%, rgba(169,210,236,0.55) 40%, rgba(255,255,255,0) 72%);
  }
  .wash-bottom-right {
    right: -40px; bottom: -50px; width: 260px; height: 240px;
    background: radial-gradient(ellipse at 70% 70%, var(--wash-deep) 0%, rgba(79,141,203,0.55) 38%, rgba(169,210,236,0.3) 60%, rgba(255,255,255,0) 76%);
  }

  .save-the-date {
    position: absolute; left: 40px; top: 34px;
    font-family: "Allura", cursive; font-weight: 400; font-size: 66px; line-height: 1;
    color: var(--sky); white-space: nowrap;
  }

  .event-title {
    position: absolute; left: 41px; top: 138px; width: 340px;
    font-family: "Poppins", sans-serif; font-weight: 600; color: var(--navy);
    line-height: 1.08;
  }
  .event-title-line { display: block; font-size: 38px; letter-spacing: -0.5px; white-space: nowrap; }

  .venue-band {
    position: absolute; left: 0; top: 288px; width: 389px; height: 34px;
    background: var(--green); color: #fff;
    font-size: 18px; font-weight: 500; line-height: 34px;
    padding-left: 41px; white-space: nowrap; letter-spacing: 0.3px;
  }

  .date-row {
    position: absolute; left: 41px; top: 332px; height: 62px;
    display: flex; align-items: center;
  }
  .weekday { font-size: 21px; font-weight: 500; padding-right: 8px; letter-spacing: -0.3px; }
  .divider { width: 1px; height: 62px; background: var(--navy); }
  .day-block { padding: 0 8px 0 12px; text-align: left; }
  .month { display: block; font-size: 12.5px; font-weight: 600; color: var(--navy); line-height: 1.1; }
  .day { display: block; font-size: 48px; font-weight: 600; color: var(--gold); line-height: 0.95; }
  .time { font-size: 23px; font-weight: 500; padding-left: 12px; letter-spacing: 1px; }

  .footer-line {
    position: absolute; left: 40px; top: 415px;
    display: flex; align-items: center; white-space: nowrap;
  }
  .address { display: flex; align-items: center; gap: 5px; font-size: 13px; font-weight: 700; }
  .address svg { width: 10px; height: 14px; }
  .footer-divider { width: 1px; height: 16px; background: var(--navy); margin: 0 11px 0 18px; }
  .honoring-label { font-size: 10.5px; font-weight: 700; color: var(--green); letter-spacing: 0.3px; margin-right: 10px; }
  .honoring-text { font-size: 9.5px; font-weight: 500; letter-spacing: 0.1px; }

  .org-name {
    position: absolute; left: 498px; top: 42px; width: 185px;
    display: flex; align-items: center; gap: 7px;
  }
  .org-dot { width: 12px; height: 12px; border-radius: 50%; background: var(--sky); flex: none; }
  .org-name-text { font-size: 20px; font-weight: 600; color: var(--navy); line-height: 1.1; }
  .org-years {
    position: absolute; left: 498px; top: 100px; width: 175px;
    font-size: 10px; font-weight: 500; letter-spacing: 2px; color: var(--navy);
    text-align: center; border-top: 1px solid var(--gold); padding-top: 3px;
  }

  .event-mark {
    position: absolute; left: 470px; top: 196px; width: 230px; text-align: center;
    font-family: "Poppins", sans-serif; font-weight: 700; color: var(--sky); line-height: 1;
  }
  .event-mark-lead { display: block; font-size: 26px; }
  .event-mark-main { display: block; font-size: 58px; letter-spacing: -1px; }
  .event-tagline {
    position: absolute; left: 470px; top: 304px; width: 230px; text-align: center;
    font-size: 16px; line-height: 1.05;
  }
  .tagline-lead { display: block; font-weight: 700; color: var(--green); }
  .tagline-rest { display: block; font-weight: 500; color: var(--ink); }
</style>
</head>
<body>
  <main class="postcard">
    <div class="wash wash-left" role="img" aria-label="Soft pale blue watercolour wash"></div>
    <div class="wash wash-top-right" role="img" aria-label="Light blue watercolour wash"></div>
    <div class="wash wash-bottom-right" role="img" aria-label="Deep blue watercolour wash with gold veins"></div>

    <h1 class="save-the-date">Save the Date</h1>

    <h2 class="event-title">
      <span class="event-title-line">50th Anniversary</span>
      <span class="event-title-line">Gala</span>
    </h2>

    <div class="venue-band">AT THE LODGE AT MARROW GLEN</div>

    <div class="date-row">
      <span class="weekday">THURSDAY</span>
      <span class="divider"></span>
      <span class="day-block"><span class="month">OCTOBER</span><span class="day">24</span></span>
      <span class="divider"></span>
      <span class="time">6-11PM</span>
    </div>

    <div class="footer-line">
      <span class="address">
        <svg viewBox="0 0 10 14" aria-hidden="true"><path d="M5 0C2.2 0 0 2.2 0 5c0 3.6 5 9 5 9s5-5.4 5-9c0-2.8-2.2-5-5-5zm0 7a2 2 0 1 1 0-4 2 2 0 0 1 0 4z" fill="#1b6b9c"/></svg>
        Sallow Brook Road, Larkhaven, NY
      </span>
      <span class="footer-divider"></span>
      <span class="honoring-label">HONORING</span>
      <span class="honoring-text">SALLOW BROOK ROAD, LARKHAVEN, NY</span>
    </div>

    <div class="org-name">
      <span class="org-dot"></span>
      <span class="org-name-text">Tidewater Reach</span>
    </div>
    <div class="org-years">1974 - 2024</div>

    <div class="event-mark">
      <span class="event-mark-lead">Threads of</span>
      <span class="event-mark-main">Grace</span>
    </div>
    <div class="event-tagline">
      <span class="tagline-lead">Celebrating 50 Years</span>
      <span class="tagline-rest">Building Community</span>
    </div>
  </main>
</body>
</html>
```